Design letter head and business card

Hello,

you should design a business card and letter paper for Kranichflug Marketing. In German we write this word with K insteat of C.

Company does not have a logo. But in general, we write Kranichflug Marketing in 2 lines.
First line red: KRANICHFLUG
Second line gray: MARKETING

Red (or wine red) and Gray / Black are our favorite colors.

Company slogan: "Fresh Ground Online Marketing".

Company offers SEO, SEM, SEA, AdWords, Conversion Optimization, Online Markting Consulting ...

The website is old, please do not use this as base for your task.

German letter paper sizes:
Viawable Dimensions : 210 x 297 mm
Needed file dimensions: 212 x 299 mm

Informations to include:

Address:
Kranichflug Marketing GmbH
Lindenweg 23
71592 Weinstadt
Germany

Geschäftsführer | CEO: Bernhard Olzner

Phone: +49 (0) 7151 846 27 05

Fax: +49 (0) 7151 846 27 88

Mail: info@kranichflug-beispiel.de

Web: www.kranichflug-beispiel.de

Amtsgericht Suttgart, HRB 537264

Bank: Rosenauer Bank
IBAN: DE827315480900XXXXXXXX
BIC: GENODES1RSQ

Thanks

Bernhard

Target Market(s)

People who likes to win the online marketing game.

Industry/Entity Type

Business

Contact Information for Business Card

Here is the personal text on the card:

Name:
Bernhard Olzner

Title:
Geschäftsführer | CEO

Address:
Kranichflug Marketing GmbH
Lindenweg 23
71592 Weinstadt
Germany

Phone:
+49 (0) 7151 846 27 05

Fax:
+49 (0) 7151 846 27 88

Mail:
olzner@kranichflug-beispiel.de

Web:
www.kranichflug-beispiel.de

Business Card:
Viewable Dimensions: 85 x 55 mm
Needed file dimensions: 87 x 57mm

Font styles to use
Sans Serif

Requirements
Nice to have
• It would be great to see the dynamics of a helicopter.

```html
<!DOCTYPE html>
<html lang="de">
<head>
<meta charset="utf-8">
<title>Kranichflug Marketing – Visitenkarte</title>
<link rel="stylesheet" href="https://fonts.googleapis.com/css2?family=Saira+Condensed:wght@300;600;700&display=swap">
<style>
  :root {
    --panel-light: #e6e6e8;
    --panel-wine: #8e1f24;
    --ink-dark: #2b2b2b;
    --ink-wine: #8e1f24;
    --ink-on-wine: #f2e6e6;
    --rule-gray: #a9a9ab;
    --illustration-top: #d9d3d4;
    --illustration-bottom: #c9b9bb;
  }
  html, body {
    margin: 0;
    padding: 0;
    width: 1200px;
    height: 654px;
    overflow: hidden;
    background: var(--panel-light);
  }
  .card {
    position: relative;
    width: 1200px;
    height: 654px;
    display: flex;
    font-family: "Saira Condensed", "Arial Narrow", sans-serif;
  }
  .card__front {
    position: relative;
    width: 647px;
    height: 100%;
    background: var(--panel-light);
  }
  .card__back {
    position: relative;
    flex: 1;
    height: 100%;
    background: var(--panel-wine);
  }
  .rule {
    position: absolute;
    top: 113px;
    height: 2px;
    background: var(--rule-gray);
  }
  .rule--left { left: 88px; width: 135px; }
  .rule--right { left: 342px; width: 215px; }
  .hero-illustration {
    position: absolute;
    left: 147px;
    top: 56px;
    width: 338px;
    height: 282px;
    border-radius: 50%;
    background: radial-gradient(ellipse at center, var(--illustration-bottom) 0%, var(--illustration-top) 55%, var(--panel-light) 75%);
  }
  .wordmark {
    position: absolute;
    left: 90px;
    top: 330px;
    width: 466px;
    height: 240px;
  }
  .wordmark__name {
    font-family: "Saira Condensed", "Arial Narrow", sans-serif;
    font-weight: 700;
    font-size: 104px;
  }
  .wordmark__name--top { fill: var(--ink-dark); }
  .wordmark__name--bottom { fill: var(--ink-wine); }
  .wordmark__slogan {
    font-family: "Saira Condensed", "Arial Narrow", sans-serif;
    font-weight: 300;
    font-size: 48px;
    fill: var(--ink-dark);
  }
  .web-address {
    position: absolute;
    left: 59px;
    top: 530px;
    margin: 0;
    font-weight: 600;
    font-size: 39px;
    line-height: 1;
    letter-spacing: 0.2px;
    white-space: nowrap;
    color: var(--ink-on-wine);
  }
</style>
</head>
<body>
  <main class="card">
    <section class="card__front">
      <div class="hero-illustration" role="img" aria-label="Illustration eines Hubschraubers mit drehendem Rotor in Rot und Grau"></div>
      <div class="rule rule--left"></div>
      <div class="rule rule--right"></div>
      <svg class="wordmark" viewBox="0 0 466 240" aria-label="Kranichflug Marketing – Fresh Ground Online Marketing">
        <text class="wordmark__name wordmark__name--top" x="0" y="86" textLength="466" lengthAdjust="spacingAndGlyphs">KRANICHFLUG</text>
        <text class="wordmark__name wordmark__name--bottom" x="0" y="167" textLength="466" lengthAdjust="spacingAndGlyphs">MARKETING</text>
        <text class="wordmark__slogan" x="0" y="230" textLength="466" lengthAdjust="spacingAndGlyphs">Fresh Ground Online Marketing</text>
      </svg>
    </section>
    <section class="card__back">
      <p class="web-address">www.kranichflug-beispiel.de</p>
    </section>
  </main>
</body>
</html>
```